Landscape design build company door flyer

I would like this flyer to convey a high-level of professionalism for a company that is excellent with communication with their clients as well as a company that does incredible installations

Went on vacation/holiday

```html
<!DOCTYPE html>
<html lang="en">
<head>
<meta charset="utf-8">
<title>Cedar Ridge Builders — Outdoor Living Flyer</title>
<link href="https://fonts.googleapis.com/css2?family=Barlow+Semi+Condensed:wght@700&family=Poppins:wght@400;500;700;800&display=swap" rel="stylesheet">
<style>
  :root {
    --navy: #0b2a40;
    --yellow: #fbb812;
    --paper: #f1f1f1;
    --ink: #111a22;
    --stage: #7f7f7f;
    --white: #ffffff;
  }
  * { box-sizing: border-box; margin: 0; padding: 0; }
  html, body {
    width: 1200px; height: 933px; overflow: hidden;
    background: var(--stage);
  }
  .flyer {
    position: absolute; left: 252px; top: 19px;
    width: 696px; height: 895px;
    background: var(--paper);
    overflow: hidden;
    font-family: "Poppins", sans-serif;
    color: var(--ink);
  }
  .hero-art { position: absolute; left: 0; top: 0; width: 696px; height: 421px; }
  .brand {
    position: absolute; left: 0; top: 96px; width: 274px;
    display: flex; align-items: center; justify-content: center; gap: 8px;
  }
  .brand-mark { width: 12px; height: 12px; background: var(--navy); }
  .brand-name {
    font-family: "Poppins", sans-serif; font-weight: 700;
    font-size: 15px; letter-spacing: 0.5px; color: var(--navy);
  }
  .headline {
    position: absolute; left: 32px; top: 182px;
    font-family: "Barlow Semi Condensed", sans-serif; font-weight: 700;
    font-size: 53px; line-height: 50.5px; color: var(--white);
    letter-spacing: 0.3px;
  }
  .headline .accent { color: var(--yellow); }
  .section-title {
    position: absolute; font-weight: 800; font-size: 21px;
    color: var(--navy); letter-spacing: -0.2px; line-height: 1;
  }
  .section-title::after {
    content: ""; position: absolute; left: 0; top: 29px;
    width: 60px; height: 3px; background: var(--yellow);
  }
  .about-title { left: 32px; top: 439px; }
  .services-title { left: 382px; top: 439px; }
  .about-text {
    position: absolute; left: 32px; top: 480px; width: 295px;
    font-size: 10.4px; line-height: 13.3px; text-align: justify;
    hyphens: auto;
  }
  .services-list {
    position: absolute; left: 382px; top: 476px; list-style: none;
  }
  .services-list li {
    display: flex; align-items: center; gap: 13px;
    height: 18.8px; font-size: 12.5px; font-weight: 500;
  }
  .services-list svg { width: 12px; height: 12px; flex: none; }
  .works-rule {
    position: absolute; left: 0; top: 643px; width: 696px; height: 1px;
    background: var(--yellow);
  }
  .works-tag {
    position: absolute; left: 245px; top: 628px; width: 197px; height: 26px;
    background: var(--yellow); color: var(--white);
    font-weight: 800; font-size: 16px; line-height: 26px; text-align: center;
  }
  .work-photo { position: absolute; top: 667px; width: 188px; height: 103px; }
  .work-deck { left: 36px; background: linear-gradient(160deg, #3f6b2f 0%, #5e7d3a 40%, #8b4a2c 70%, #a65a36 100%); }
  .work-pool { left: 250px; background: linear-gradient(135deg, #4b5a4a 0%, #c9cfd0 35%, #4fb9b8 55%, #d6dadb 75%, #9aa2a4 100%); }
  .work-firepit { left: 464px; background: linear-gradient(170deg, #3a3f3a 0%, #4f7fa0 30%, #5b4e45 60%, #8a6a4c 100%); }
  .footer-art { position: absolute; left: 0; top: 806px; width: 696px; height: 89px; }
  .phone {
    position: absolute; left: 43px; top: 831px;
    display: flex; align-items: center; gap: 11px;
    font-weight: 800; font-size: 34px; line-height: 38px; color: var(--yellow);
    letter-spacing: -0.5px;
  }
  .phone svg { width: 25px; height: 25px; }
  .contact { position: absolute; left: 462px; top: 824px; list-style: none; }
  .contact li {
    display: flex; align-items: center; gap: 11px;
    height: 23px; font-size: 12.5px; font-weight: 500; color: var(--white);
  }
  .contact svg { width: 15px; height: 13px; flex: none; }
</style>
</head>
<body>
<main class="flyer">
  <svg class="hero-art" viewBox="0 0 696 421" aria-hidden="false">
    <defs>
      <linearGradient id="heroPhotoTone" x1="0" y1="0" x2="1" y2="1">
        <stop offset="0" stop-color="#5d7a3a"/>
        <stop offset="0.35" stop-color="#6f7880"/>
        <stop offset="0.7" stop-color="#5a6168"/>
        <stop offset="1" stop-color="#4a3a2e"/>
      </linearGradient>
    </defs>
    <polygon role="img" aria-label="Aerial photo of a two-storey home with a new paver driveway, steps and planting beds"
      points="319,0 696,0 696,421 464,421 270,142" fill="url(#heroPhotoTone)"/>
    <polygon class="hero-panel" points="0,142 324,142 464,421 0,421" fill="var(--navy)"/>
  </svg>

  <div class="brand">
    <span class="brand-mark"></span>
    <span class="brand-name">CEDAR RIDGE BUILDERS</span>
  </div>

  <h1 class="headline">
    LET’S CREATE<br>YOUR DREAM<br>
    <span class="accent">OUTDOOR<br>LIVING SPACE!</span>
  </h1>

  <h2 class="section-title about-title">ABOUT US</h2>
  <p class="about-text">Discover the endless possibilities for your outdoor space with The Cedar Ridge Team. Our team of skilled artisans is dedicated to turning your outdoor space into a breathtaking oasis that you’ll love coming home to. Whether it’s a cozy patio for intimate gatherings, a sprawling deck to host memorable parties, or a custom paver driveway that adds instant curb appeal, our high-quality craftsmanship ensures stunning results that exceed your expectations.</p>

  <h2 class="section-title services-title">OUR SERVICES</h2>
  <ul class="services-list">
    <li><svg viewBox="0 0 12 12"><circle cx="6" cy="6" r="6" fill="var(--navy)"/><path d="M3.2 6.2l1.9 1.9 3.8-4" stroke="#fff" stroke-width="1.6" fill="none"/></svg>Paver Patios</li>
    <li><svg viewBox="0 0 12 12"><circle cx="6" cy="6" r="6" fill="var(--navy)"/><path d="M3.2 6.2l1.9 1.9 3.8-4" stroke="#fff" stroke-width="1.6" fill="none"/></svg>Paver Driveways</li>
    <li><svg viewBox="0 0 12 12"><circle cx="6" cy="6" r="6" fill="var(--navy)"/><path d="M3.2 6.2l1.9 1.9 3.8-4" stroke="#fff" stroke-width="1.6" fill="none"/></svg>Retaining Walls</li>
    <li><svg viewBox="0 0 12 12"><circle cx="6" cy="6" r="6" fill="var(--navy)"/><path d="M3.2 6.2l1.9 1.9 3.8-4" stroke="#fff" stroke-width="1.6" fill="none"/></svg>Decks &amp; Railings</li>
    <li><svg viewBox="0 0 12 12"><circle cx="6" cy="6" r="6" fill="var(--navy)"/><path d="M3.2 6.2l1.9 1.9 3.8-4" stroke="#fff" stroke-width="1.6" fill="none"/></svg>Pools</li>
    <li><svg viewBox="0 0 12 12"><circle cx="6" cy="6" r="6" fill="var(--navy)"/><path d="M3.2 6.2l1.9 1.9 3.8-4" stroke="#fff" stroke-width="1.6" fill="none"/></svg>Outdoor Lighting</li>
    <li><svg viewBox="0 0 12 12"><circle cx="6" cy="6" r="6" fill="var(--navy)"/><path d="M3.2 6.2l1.9 1.9 3.8-4" stroke="#fff" stroke-width="1.6" fill="none"/></svg>Firepits &amp; Fireplaces</li>
  </ul>

  <div class="works-rule"></div>
  <div class="works-tag">OUR WORKS</div>

  <div class="work-photo work-deck" role="img" aria-label="Wooden deck with pergola and patio chairs among trees"></div>
  <div class="work-photo work-pool" role="img" aria-label="Aerial view of a small pool surrounded by white composite decking"></div>
  <div class="work-photo work-firepit" role="img" aria-label="Evening patio with round firepit, lit seat walls and pool behind"></div>

  <svg class="footer-art" viewBox="0 0 696 89" aria-hidden="true">
    <rect x="0" y="7" width="696" height="82" fill="var(--navy)"/>
    <polygon points="425,0 696,0 696,89 386,89" fill="var(--yellow)"/>
  </svg>

  <div class="phone">
    <svg viewBox="0 0 24 24"><path d="M6.6 2.5l3 3.6-2 2.4c1.3 2.9 3.6 5.3 6.6 6.8l2.4-2 3.6 3-1.6 3.9C10 19.8 3.9 13.6 3 4.2z" fill="var(--yellow)"/></svg>
    <span>206-555-0142</span>
  </div>

  <ul class="contact">
    <li><svg viewBox="0 0 15 13"><rect x="0.5" y="1.5" width="14" height="10" fill="#fff"/><path d="M0.5 1.8l7 5.2 7-5.2" stroke="var(--yellow)" stroke-width="1.4" fill="none"/></svg>info@cedarridgebuilders.com</li>
    <li><svg viewBox="0 0 15 13"><circle cx="7.5" cy="6.5" r="5.8" stroke="#fff" stroke-width="1.1" fill="none"/><ellipse cx="7.5" cy="6.5" rx="2.4" ry="5.8" stroke="#fff" stroke-width="1" fill="none"/><path d="M1.7 6.5h11.6" stroke="#fff" stroke-width="1"/></svg>www.cedarridgebuilders.com</li>
  </ul>
</main>
</body>
</html>
```